New Corporate Email Signature with Custom GIF KAV Electric LLC & KAV Fire & Security

Project Overview
KAV Electric LLC and KAV Fire & Security are seeking a professional, polished, and technically robust corporate email signature design. The project has two integrated deliverables:
A custom animated GIF representing both sides of our business
A complete corporate email signature layout designed for real-world compatibility (Gmail, Outlook, iOS, Android)
Our brand aesthetic is corporate, conservative, and clean. We value clarity, trust, professionalism, and subtle creativity β€” nothing overly flashy or cartoonish.
This design will be used across the entire company and must be visually aligned with our brand while remaining technically dependable.

PART 1 β€” Animated GIF Requirements
The GIF will be the core visual anchor of the new signature.
It must be clean, smooth, subtle, and optimized for email use.
βš™ Technical Requirements
Max file size: 150–200 KB (smaller is better)
Dimensions: approx 300px width (flexible, but must look good small)
Looping: continuous loop
Style: professional, minimalistic transitions

No rapid flashing or harsh animations
Must export cleanly into a format email clients accept

🎞 GIF Animation Sequence
Phase 1 β€” KAV Electric (KE)
Use the yellow β€œKE” avatar logo (provided).
Animation flow:
KE avatar appears
Full name β€œKAV Electric LLC” slides in, fades in, or otherwise appears smoothly
A scrolling or cycling list of service offerings displays:
EV Charging Stations
Generator & Transformers
Testing & Troubleshooting
LED Lighting Upgrades
After the list is shown, the entire KE segment fades out

Phase 2 β€” KAV Fire & Security (KF)
Use the red β€œKF” avatar logo (provided).
Animation flow mirrors Phase 1:
KF avatar appears
Full name β€œKAV Fire & Security” slides/fades in
Scrolling or cycling list of services displays:
Fire Alarm Upgrades
BQTL 48 Test & Inspect
Security Surveillance Systems
Access Control Systems
Data & Fiber Optic Cabling
Fade out β†’ loop back to KE
Creative Direction

Designers are encouraged to use:
Clean transitions
Soft fades
Professional typography
Modern minimalism
Consistent brand colors
High clarity at small sizes

Avoid:
Busy motion
Hard flashes
Excessive text overlays
Overly long transitions

The goal: a smooth, corporate-grade rotation that fits seamlessly into an email signature.

PART 2 β€” Corporate Email Signature Design

The signature must be visually appealing, brand-aligned, and structurally bulletproof across all major email systems.
πŸ“ Required Elements
πŸ‘€ Left Side Content
Circular headshot (we will supply final photos)
Social media icons with embedded URLs:
Facebook
LinkedIn
Google Business Profile
Instagram

Icons should be clean, modern, and in alignment with brand colors
πŸ“„ Right Side Content
Name
Title
KAV Electric LLC / KAV Fire & Security (depending on user)
Phone number
Email address
License# 52804
Physical office address: 384 Pembrook St, Westwood NJ 07912

Small CTA for newsletter signup (button or micro-banner)

🏒 Branding Assets Provided

You will receive:
KE avatar logo
KF avatar logo
Full-name KE logo
Full-name KF logo

These should be incorporated naturally and professionally.

Design Requirements

Conservative corporate styling

Clean typography

Balanced use of white space

Professional hierarchy

Light and dark mode compatibility preferred

Layout should not rely on one large image

All images should export cleanly for hosting on servers/CDN

Avoid overly tall signatures

The final signature must present as modern, trustworthy, and technically reliable across platforms.

πŸ§ͺ Compatibility Requirements

The signature must display correctly in:

Gmail (web and mobile)

Outlook (desktop & online)

Apple Mail

iPhone Mail

Android mail apps

Designers must avoid DIV-based layouts and instead propose a layout that can be implemented using table-based HTML, which is the industry standard for email compatibility.

You do not need to build the HTML β€” only supply the final layered design (PSD/AI/Figma) plus a clear structural layout that can be converted to HTML later.

πŸ“¦ Deliverables
1. Animated GIF

Final optimized GIF

Source file (After Effects, Photoshop, or equivalent)

Export guidelines so we can reproduce future versions

2. Email Signature Design

Full static design mockup

Modular layout for each employee

Icon set for social media

Newsletter CTA element

Clear spacing, alignment, and typography specifications

All source files (PSD, AI, Figma, etc.)

🧭 Creative Guidance Summary

We want:
βœ” Modern
βœ” Corporate
βœ” Minimalistic
βœ” Professional
βœ” Clean motion
βœ” Consistent branding
βœ” Email-safe elements

We do not want:
✘ Flashy marketing look
✘ Overly colorful or playful styles
✘ Hard-to-read fonts
✘ Heavy animation
✘ Oversized signatures

πŸ›  Tools & Format Flexibility

We allow full creative freedom regarding:

Animation style

Typography choices

Structuring of the two-column layout

How the service lists scroll or cycle

As long as the end result is clean, brand-aligned, professional, and email-compatible.

πŸ’¬ Final Note to Designers

We encourage creativity within the boundaries of corporate professionalism.
This signature will represent our company every time an email is sent β€” it must communicate trust, clarity, expertise, and brand strength.

```html
<!DOCTYPE html>
<html lang="en">
<head>
<meta charset="utf-8">
<title>KAV Email Signatures</title>
<link rel="stylesheet" href="https://fonts.googleapis.com/css2?family=Lato:wght@400;700;900&display=swap">
<style>
  :root {
    --page-bg: #ebebeb;
    --card-bg: #ffffff;
    --fire-red: #e1001a;
    --electric-yellow: #e8cc12;
    --ink: #111111;
    --muted: #7a7a7a;
    --band-gray: #808080;
    --rule: #c9c9c9;
    --white: #ffffff;
  }
  * { margin: 0; padding: 0; box-sizing: border-box; }
  html, body { width: 1200px; height: 769px; overflow: hidden; background: var(--page-bg); font-family: "Lato", Arial, sans-serif; }
  .stage { position: relative; width: 1200px; height: 769px; }

  .signature { position: absolute; left: 70px; width: 1046px; height: 262px; background: var(--card-bg); overflow: hidden; }
  .signature--fire { top: 78px; }
  .signature--electric { top: 413px; }

  .stripe { position: absolute; top: 0; height: 100%; background: var(--fire-red); }
  .texture { position: absolute; right: 0; top: 0; width: 560px; height: 100%;
    background: radial-gradient(ellipse at 70% 60%, #e4e4e4 0%, #f3f3f3 40%, rgba(255,255,255,0) 75%); }

  .headshot { position: absolute; border-radius: 50%;
    background: radial-gradient(circle at 50% 40%, #c9b7a3 0%, #7f7a78 45%, #3c4450 100%); }

  .social { position: absolute; width: 32px; height: 32px; border-radius: 50%; }
  .social--fire { background: var(--fire-red); }
  .social--electric { background: var(--electric-yellow); }

  .divider { position: absolute; width: 2px; background: var(--rule); }

  .name { position: absolute; font-weight: 900; font-size: 28px; line-height: 1; white-space: nowrap; }
  .name .title { font-weight: 400; font-size: 22px; color: var(--muted); margin-left: 8px; }
  .signature--fire .name { color: var(--ink); }
  .signature--electric .name { color: var(--muted); }
  .role { position: absolute; font-size: 22px; color: var(--muted); line-height: 1; }

  .company { position: absolute; font-weight: 900; font-size: 36px; letter-spacing: 5px; line-height: 1; text-transform: uppercase; white-space: nowrap; }
  .signature--fire .company { color: var(--fire-red); }
  .signature--electric .company { color: var(--muted); letter-spacing: 6px; }

  .license { position: absolute; font-weight: 700; font-size: 21px; color: var(--muted); line-height: 1; }

  .contact { position: absolute; display: flex; align-items: center; gap: 10px; font-size: 21px; color: var(--ink); white-space: nowrap; line-height: 1; }
  .contact svg { flex: none; }

  .cta { position: absolute; display: flex; align-items: center; justify-content: center; border-radius: 26px;
    color: var(--white); font-weight: 900; font-size: 21px; letter-spacing: .3px; }
  .cta--fire { background: var(--fire-red); }
  .cta--electric { background: var(--electric-yellow); }

  .contact-band { position: absolute; left: 0; bottom: 0; width: 100%; height: 61px; background: var(--band-gray); }
  .contact-band .contact { color: var(--white); font-weight: 700; font-size: 19px; top: 11px; }
  .icon-disc { width: 40px; height: 40px; border-radius: 50%; background: var(--electric-yellow); display: flex; align-items: center; justify-content: center; }
</style>
</head>
<body>
<main class="stage">

  <section class="signature signature--fire">
    <div class="stripe" style="left:0;width:14px"></div>
    <div class="stripe" style="left:20px;width:6px"></div>
    <div class="stripe" style="left:31px;width:6px"></div>
    <div class="texture" role="img" aria-label="Soft grey flowing line texture"></div>

    <div class="headshot" role="img" aria-label="Circular headshot of Mark Hale" style="left:54px;top:24px;width:156px;height:156px"></div>

    <span class="social social--fire" style="left:57px;top:199px"></span>
    <span class="social social--fire" style="left:97px;top:199px"></span>
    <span class="social social--fire" style="left:137px;top:199px"></span>
    <span class="social social--fire" style="left:177px;top:199px"></span>

    <div class="divider" style="left:251px;top:53px;height:157px"></div>

    <div class="name" style="left:282px;top:33px">MARK HALE<span class="title">Digital Marketing</span></div>
    <div class="company" style="left:282px;top:76px">KAV Fire &amp; Security</div>

    <div class="contact" style="left:282px;top:128px">
      <svg width="24" height="24" viewBox="0 0 24 24"><circle cx="12" cy="12" r="12" fill="var(--fire-red)"/><path d="M8.5 6.5l2 2.3-1.2 1.5c.8 1.7 2 2.9 3.6 3.7l1.5-1.2 2.3 2-1.3 1.7c-3.9-.5-7.5-4.1-8.1-8.3z" fill="#fff"/></svg>
      +1 555 0142 3390
    </div>
    <div class="contact" style="left:535px;top:126px">
      <svg width="24" height="24" viewBox="0 0 24 24"><circle cx="12" cy="12" r="11" fill="none" stroke="var(--fire-red)" stroke-width="2"/><rect x="6.5" y="8" width="11" height="8" rx="1" fill="var(--fire-red)"/><path d="M6.8 8.6l5.2 4 5.2-4" fill="none" stroke="#fff" stroke-width="1.2"/></svg>
      info@kavfire.com
    </div>
    <div class="contact" style="left:282px;top:170px">
      <svg width="24" height="24" viewBox="0 0 24 24"><circle cx="12" cy="12" r="12" fill="var(--fire-red)"/><path d="M12 5a4.5 4.5 0 0 0-4.5 4.5c0 3.3 4.5 8.5 4.5 8.5s4.5-5.2 4.5-8.5A4.5 4.5 0 0 0 12 5z" fill="#fff"/><circle cx="12" cy="9.6" r="1.7" fill="var(--fire-red)"/></svg>
      384 Pembrook St, Brennick Vale VT 07912
    </div>
    <div class="license" style="left:284px;top:219px">LICENSE# 52804</div>

    <div class="cta cta--fire" style="left:758px;top:178px;width:232px;height:51px">STAY CONNECTED</div>
  </section>

  <section class="signature signature--electric">
    <div class="headshot" role="img" aria-label="Circular headshot of Mark Hale" style="left:68px;top:20px;width:114px;height:114px"></div>

    <span class="social social--electric" style="left:52px;top:148px"></span>
    <span class="social social--electric" style="left:92px;top:148px"></span>
    <span class="social social--electric" style="left:132px;top:148px"></span>
    <span class="social social--electric" style="left:170px;top:148px"></span>

    <div class="divider" style="left:297px;top:0;height:201px"></div>
    <div class="divider" style="left:303px;top:0;height:201px"></div>

    <div class="name" style="left:335px;top:30px">MARK HALE</div>
    <div class="role" style="left:335px;top:70px">Digital Marketing</div>
    <div class="company" style="left:335px;top:103px">KAV Electric LLC</div>
    <div class="license" style="left:337px;top:156px">LICENSE# 52804</div>

    <div class="cta cta--electric" style="left:776px;top:126px;width:234px;height:51px">STAY CONNECTED</div>

    <div class="contact-band">
      <div class="contact" style="left:53px">
        <span class="icon-disc"><svg width="20" height="20" viewBox="0 0 24 24"><path d="M6 3l3.3 3.8-2 2.5c1.3 2.8 3.4 4.8 6.1 6.1l2.5-2 3.8 3.3-2.1 2.8C11 19 5 13 4.1 6z" fill="#fff"/></svg></span>
        5550142339
      </div>
      <div class="contact" style="left:266px">
        <span class="icon-disc"><svg width="20" height="20" viewBox="0 0 24 24"><rect x="3" y="6" width="18" height="12" rx="1.5" fill="none" stroke="#fff" stroke-width="2"/><path d="M3.5 7l8.5 6.5L20.5 7" fill="none" stroke="#fff" stroke-width="2"/></svg></span>
        info@kavelectric.com
      </div>
      <div class="contact" style="left:581px">
        <span class="icon-disc"><svg width="20" height="20" viewBox="0 0 24 24"><path d="M12 2a7 7 0 0 0-7 7c0 5.2 7 13 7 13s7-7.8 7-13a7 7 0 0 0-7-7z" fill="#fff"/><circle cx="12" cy="9" r="2.6" fill="var(--electric-yellow)"/></svg></span>
        384 Pembrook St, Brennick Vale VT 07912
      </div>
    </div>
  </section>

</main>
</body>
</html>
```